real esate business card with company logo and name

we need a business card design for a real esate company

The company name is Walsh & Brand Pty Ltd, and we have our logo designed and will upload. We want classic or moden feel. Black or white background. looks more textured. Should include folowinginformations
Owen Walsh and Lucy Brand
Sales Agents & Onsite Manager
p: 07 5948 2063
F: 07 5948 2174
M:0431 857 219
3/42 Marlow Crescent, FERNLEA QLD 4213

We want this business card looks professonal. Thank you in advance.

Industry/Entity Type

Real Estate Agent

Contact Information for Business Card

Owen Walsh and Lucy Brand
Onsite Manager & Sales Agents
p: 07 5948 2063
M:0431 857 219

Font styles to use
Serif

Colors
000000
fbfbfb
333333
959595

Requirements
Must have
• company logo and name, black or white back ground

```html
<!DOCTYPE html>
<html lang="en">
<head>
<meta charset="utf-8">
<title>Walsh &amp; Brand Pty Ltd – Business Card</title>
<link rel="stylesheet" href="https://fonts.googleapis.com/css2?family=Fira+Sans+Condensed:wght@400;500;600&display=swap">
<style>
  :root {
    --ink: #000000;
    --paper: #fbfbfb;
    --charcoal: #333333;
    --silver: #959595;
    --frost: #e6e6e6;
    --text-light: #f2f2f2;
    --text-muted: #d0d0d0;
    --page: #cfcfcf;
  }
  html, body {
    margin: 0;
    width: 1200px;
    height: 969px;
    overflow: hidden;
    background: var(--page);
    font-family: "Fira Sans Condensed", "Arial Narrow", sans-serif;
  }
  .business-card {
    position: absolute;
    left: 100px;
    top: 201px;
    width: 1000px;
    height: 567px;
    background: linear-gradient(160deg, var(--paper) 0%, var(--frost) 55%, #d8d8d8 100%);
    box-shadow: 0 18px 40px rgba(0,0,0,0.25);
    overflow: hidden;
  }
  .card-shapes {
    position: absolute;
    inset: 0;
    width: 1000px;
    height: 567px;
  }
  .contact-block {
    position: absolute;
    left: 42px;
    top: 128px;
    color: var(--text-light);
  }
  .agent-names {
    margin: 0;
    font-size: 33px;
    font-weight: 400;
    letter-spacing: 0.3px;
    line-height: 40px;
  }
  .agent-roles {
    margin: 2px 0 0;
    font-size: 25px;
    font-weight: 400;
    color: var(--text-muted);
    line-height: 32px;
  }
  .phone-list {
    list-style: none;
    margin: 22px 0 0;
    padding: 0;
  }
  .phone-list li {
    display: flex;
    align-items: center;
    gap: 14px;
    height: 38px;
    font-size: 23px;
    color: var(--text-muted);
  }
  .phone-list svg {
    width: 22px;
    height: 22px;
    fill: var(--text-muted);
  }
  .office-address {
    margin: 16px 0 0;
    font-style: normal;
    font-size: 23px;
    line-height: 32px;
    color: var(--silver);
  }
  .company-name {
    position: absolute;
    left: 560px;
    top: 378px;
    width: 380px;
    text-align: center;
    margin: 0;
    font-size: 26px;
    font-weight: 600;
    letter-spacing: 1.5px;
    color: var(--charcoal);
    text-transform: uppercase;
  }
</style>
</head>
<body>
  <section class="business-card">
    <svg class="card-shapes" viewBox="0 0 1000 567" aria-hidden="true">
      <defs>
        <linearGradient id="dark-panel" x1="0" y1="0" x2="1" y2="0.3">
          <stop offset="0" stop-color="#3a3a3a"/>
          <stop offset="0.55" stop-color="#1c1c1c"/>
          <stop offset="1" stop-color="#000000"/>
        </linearGradient>
      </defs>
      <polygon class="dark-panel" points="0,0 664,0 455,89 442,450 664,567 0,567" fill="url(#dark-panel)"/>
      <polyline class="frame-line" points="664,0 455,89 442,450 664,567" fill="none" stroke="#fbfbfb" stroke-opacity="0.75" stroke-width="3"/>
      <polyline class="frame-line" points="690,0 470,95 458,442 690,567" fill="none" stroke="#959595" stroke-opacity="0.5" stroke-width="2"/>
    </svg>

    <div class="contact-block">
      <h1 class="agent-names">Owen Walsh &amp; Lucy Brand</h1>
      <p class="agent-roles">Sales Agents &amp; Onsite Manager</p>
      <ul class="phone-list">
        <li>
          <svg viewBox="0 0 24 24" aria-label="Phone"><path d="M6.6 10.8c1.4 2.8 3.8 5.1 6.6 6.6l2.2-2.2c.3-.3.7-.4 1-.2 1.1.4 2.3.6 3.6.6.6 0 1 .4 1 1V20c0 .6-.4 1-1 1C10.6 21 3 13.4 3 4c0-.6.4-1 1-1h3.5c.6 0 1 .4 1 1 0 1.3.2 2.5.6 3.6.1.3 0 .7-.2 1z"/></svg>
          <span>07 5948 2063</span>
        </li>
        <li>
          <svg viewBox="0 0 24 24" aria-label="Mobile"><path d="M7 1h10c1.1 0 2 .9 2 2v18c0 1.1-.9 2-2 2H7c-1.1 0-2-.9-2-2V3c0-1.1.9-2 2-2zm0 4v13h10V5z"/></svg>
          <span>0431 857 219</span>
        </li>
        <li>
          <svg viewBox="0 0 24 24" aria-label="Fax"><path d="M6 2h9l3 3v5H6zM3 11h18c1.1 0 2 .9 2 2v7c0 1.1-.9 2-2 2H3c-1.1 0-2-.9-2-2v-7c0-1.1.9-2 2-2zm3 3v2h5v-2zm0 3v2h5v-2z"/></svg>
          <span>07 5948 2174</span>
        </li>
      </ul>
      <address class="office-address">3/42 Marlow Crescent<br>FERNLEA QLD 4213</address>
    </div>

    <p class="company-name">Walsh &amp; Brand Pty Ltd.</p>
  </section>
</body>
</html>
```